Business Card - connecting 2 souls and beggining the journey of self discovery

Logo on the front
with tag line

On the back list of services and contact details

Seminars
workshops
Coaching
podcasts

Darren Whitlow
Health & Wellbeing Life Coach
0491 372 615
darren@brightcoreliving.example
brightcoreliving.example

Industry/Entity Type

Life Coaching

Contact Information for Business Card

I like the use of colour from the logo to be used. I'm not a fan of white.

Requirements
Must have
• My tagline: The journey home starts with you
Nice to have
• Use of colour that is in the mind body soul logo

```html
<!DOCTYPE html>
<html lang="en">
<head>
<meta charset="utf-8">
<title>Brightcore Living – Business Card</title>
<link href="https://fonts.googleapis.com/css2?family=Montserrat:wght@500&family=Open+Sans:wght@400;600;700&display=swap" rel="stylesheet">
<style>
  :root {
    --charcoal: #333333;
    --charcoal-light: #3c3c3c;
    --orange: #f07f1d;
    --white: #ffffff;
    --ink: #2e2e2e;
    --grey: #6a6a6a;
    --grey-soft: #858585;
    --backdrop: #e6e6e6;
  }
  * { margin: 0; padding: 0; box-sizing: border-box; }
  html, body { width: 1200px; height: 1000px; overflow: hidden; }
  body { background: var(--backdrop); font-family: "Open Sans", Arial, sans-serif; position: relative; }

  .card { position: absolute; left: 200px; width: 800px; height: 457px; overflow: hidden;
          background: var(--charcoal); box-shadow: 0 6px 18px rgba(0,0,0,.18); }
  .card--front { top: 30px; }
  .card--back { top: 513px; }
  .card__shapes { position: absolute; inset: 0; }

  /* Front */
  .brand-mark { position: absolute; left: 0; right: 0; top: 80px; display: flex; flex-direction: column; align-items: center; }
  .brand-mark__dot { width: 78px; height: 78px; border-radius: 50%; background: var(--orange); }
  .brand-mark__name { margin-top: 22px; font-family: "Montserrat", Arial, sans-serif; font-weight: 500;
                      font-size: 40px; color: var(--white); letter-spacing: -0.5px; }
  .tagline { position: absolute; left: 46px; bottom: 26px; font-size: 13px; font-weight: 600;
             letter-spacing: 4.5px; text-transform: uppercase; color: var(--orange); }
  .front-web { position: absolute; right: 26px; top: 374px; font-size: 17px; color: var(--ink); }
  .accent { color: var(--orange); }

  /* Back */
  .side-brand { position: absolute; left: 40px; top: 90px; display: flex; align-items: center; gap: 18px; }
  .side-brand__dot { width: 62px; height: 62px; border-radius: 50%; background: var(--orange); }
  .side-brand__name { position: absolute; left: 170px; top: 60px; transform-origin: left top; transform: rotate(-90deg) translateX(-300px);
                      font-family: "Montserrat", Arial, sans-serif; font-weight: 500; font-size: 36px; color: var(--white); white-space: nowrap; }
  .side-brand-dot { position: absolute; left: 70px; top: 170px; width: 62px; height: 62px; border-radius: 50%; background: var(--orange); }

  .contact { position: absolute; left: 400px; top: 48px; color: var(--ink); }
  .contact__name { font-size: 28px; font-weight: 700; color: var(--orange); line-height: 1.1; }
  .contact__role { font-size: 20px; font-weight: 600; color: var(--grey); }
  .contact__pin { margin-top: 38px; width: 18px; height: 18px; display: block; }
  .contact__address { margin-top: 8px; font-size: 17px; line-height: 1.25; }
  .contact__list { list-style: none; margin-top: 64px; font-size: 17px; line-height: 1.35; }
  .contact__list li { display: flex; align-items: center; gap: 12px; }
  .contact__list svg { width: 16px; height: 16px; flex: none; }
  .services { position: absolute; left: 390px; bottom: 26px; font-size: 18px; font-weight: 600;
              color: var(--grey-soft); letter-spacing: .3px; word-spacing: 2px; }
</style>
</head>
<body>

<section class="card card--front" aria-label="Card front">
  <svg class="card__shapes" viewBox="0 0 800 457" width="800" height="457">
    <defs>
      <radialGradient id="mapTone" cx="50%" cy="40%" r="70%">
        <stop offset="0" stop-color="#3d3d3d"/>
        <stop offset="1" stop-color="#323232"/>
      </radialGradient>
    </defs>
    <rect width="800" height="457" fill="url(#mapTone)" role="img" aria-label="Faint world map backdrop"/>
    <path d="M548 330 L800 330 L800 457 L420 457 L520 350 Q532 330 548 330 Z" fill="var(--orange)"/>
    <path d="M562 340 L800 340 L800 457 L440 457 L534 360 Q546 340 562 340 Z" fill="var(--white)"/>
  </svg>
  <div class="brand-mark">
    <span class="brand-mark__dot"></span>
    <span class="brand-mark__name">Brightcore Living</span>
  </div>
  <p class="tagline">The journey home starts with you</p>
  <p class="front-web">www.<span class="accent">brightcoreliving</span>.example</p>
</section>

<section class="card card--back" aria-label="Card back">
  <svg class="card__shapes" viewBox="0 0 800 457" width="800" height="457">
    <rect width="800" height="457" fill="url(#mapTone)" role="img" aria-label="Faint world map backdrop"/>
    <path d="M370 0 L800 0 L800 457 L228 457 L290 200 Q300 160 338 140 Q364 126 370 100 Z" fill="var(--orange)"/>
    <path d="M380 0 L800 0 L800 457 L242 457 L302 200 Q312 160 350 140 Q376 126 380 100 Z" fill="var(--white)"/>
  </svg>
  <span class="side-brand-dot"></span>
  <span class="side-brand__name">Brightcore Living</span>

  <div class="contact">
    <p class="contact__name">Darren Whitlow</p>
    <p class="contact__role">Life Coach</p>
    <svg class="contact__pin" viewBox="0 0 18 18" aria-hidden="true">
      <path d="M16 2 L2 8 L8 10 L10 16 Z" fill="none" stroke="var(--orange)" stroke-width="1.4" stroke-linejoin="round"/>
    </svg>
    <p class="contact__address">Your Street Address here<br>Country Name,123</p>
    <ul class="contact__list">
      <li><svg viewBox="0 0 16 16" aria-hidden="true"><rect x="4" y="1" width="8" height="14" rx="1.5" fill="none" stroke="var(--orange)" stroke-width="1.4"/><circle cx="8" cy="12.5" r=".9" fill="var(--orange)"/></svg>0491 372 615</li>
      <li><svg viewBox="0 0 16 16" aria-hidden="true"><rect x="1" y="3" width="14" height="10" fill="var(--orange)"/><path d="M1 3 L8 9 L15 3" fill="none" stroke="var(--white)" stroke-width="1.2"/></svg>darren@brightcoreliving.example</li>
      <li><svg viewBox="0 0 16 16" aria-hidden="true"><circle cx="8" cy="8" r="7" fill="var(--orange)"/><path d="M1 8 H15 M8 1 C4 5 4 11 8 15 M8 1 C12 5 12 11 8 15" fill="none" stroke="var(--white)" stroke-width="1"/></svg>www.<span class="accent">brightcoreliving</span>.example</li>
    </ul>
  </div>
  <p class="services">Seminars | Workshops | Coaching | Podcasts</p>
</section>

</body>
</html>
```